Stylish Business Cards Wanted

- DOUBLE SIDED Design Required -

High end, edgy cards for a corporate and personal stylist. Must include logo,
Name: Belinda Harwick
Title: Director and Stylist
telephone : +61 8 7142 5809
email: belinda@theloombriefing.example
website: theloombriefing.example
Tag: Corporate Workwear & Uniform Specialist | Personal Stylist
Would like nice icons for telephone, email, website

Target Market(s)

Businesses wanting stylish uniforms, people wanting stylish wardrobes

Industry/Entity Type

Corporate Workwear Stylist

Contact Information for Business Card

I would like black, white and gold foiling incorporated in the design - possibly a touch of the other colours on my branding guide attached Name: Belinda Harwick Title: Director and Stylist telephone : +61 8 7142 5809 email: belinda@theloombriefing.example website: theloombriefing.example Tag: Corporate Workwear & Uniform Specialist | Personal Stylist Would like nice icons for telephone, email, website

Font styles to use
Other font styles liked:
• Raleway

Colors

Designer to choose colors to be used in the design.

Requirements
Must have
• Gold foil accents

```html
<!DOCTYPE html>
<html lang="en">
<head>
<meta charset="utf-8">
<title>The Loom Briefing – Business Cards</title>
<link href="https://fonts.googleapis.com/css2?family=Questrial&family=Raleway:wght@400;600;700&display=swap" rel="stylesheet">
<style>
  :root{
    --backdrop:#ececec;
    --paper:#ffffff;
    --gold:#e4bc57;
    --ink:#1d1b1b;
    --white:#ffffff;
    --rule:#3a3a3a;
  }
  *{box-sizing:border-box;margin:0;padding:0}
  html,body{width:1200px;height:507px;overflow:hidden;background:var(--backdrop)}
  .canvas{position:relative;width:1200px;height:507px}
  .card{position:absolute;top:106px;width:492px;height:295px;overflow:hidden}
  .card--front{left:84px;background:var(--paper);border:1px solid #d6d6d6}
  .card--back{left:624px;background:var(--gold)}

  /* front */
  .brand{position:absolute;left:0;right:0;top:112px;text-align:center;
    font-family:"Raleway",sans-serif;font-weight:700;font-size:36px;
    letter-spacing:.5px;color:var(--ink)}
  .tagline{position:absolute;left:55px;top:221px;width:383px;height:25px;
    border:1px solid var(--rule);display:flex;align-items:center;justify-content:center;
    padding:0 4px;
    font-family:"Questrial",sans-serif;font-size:10.9px;letter-spacing:-.1px;
    color:var(--ink);white-space:nowrap}
  .tagline .sep{margin:0 4px}

  /* back */
  .name-bar{position:absolute;left:0;top:131px;width:30px;height:19px;background:var(--ink)}
  .identity{position:absolute;right:289px;top:127px;text-align:right;white-space:nowrap}
  .identity__name{font-family:"Raleway",sans-serif;font-weight:700;font-size:21px;color:var(--ink);line-height:1.1}
  .identity__title{font-family:"Questrial",sans-serif;font-size:11px;color:var(--white);margin-top:2px}
  .divider{position:absolute;left:212px;top:117px;width:1px;height:60px;background:var(--ink)}
  .contacts{position:absolute;left:220px;top:117px;list-style:none}
  .contacts li{display:flex;align-items:center;height:21.5px;
    font-family:"Questrial",sans-serif;font-size:14px;color:var(--white);white-space:nowrap}
  .contacts svg{width:11px;height:11px;margin-right:6px;flex:none}
</style>
</head>
<body>
<div class="canvas">

  <section class="card card--front">
    <div class="brand">The Loom Briefing</div>
    <div class="tagline">
      <span>CORPORATE WORKWEAR</span><span class="sep">|</span>
      <span>UNIFORM SPECIALIST</span><span class="sep">|</span>
      <span>PERSONAL STYLIST</span>
    </div>
  </section>

  <section class="card card--back">
    <div class="name-bar"></div>
    <div class="identity">
      <div class="identity__name">Belinda Harwick</div>
      <div class="identity__title">Director and Stylist</div>
    </div>
    <div class="divider"></div>
    <ul class="contacts">
      <li>
        <svg viewBox="0 0 12 12" aria-hidden="true"><circle cx="6" cy="6" r="6" fill="#1d1b1b"/><path d="M3 5.2c0-1 1-1.6 3-1.6s3 .6 3 1.6l-1 .3-.4-.8H4.4l-.4.8zM3.8 8.6l.6-2.4h3.2l.6 2.4z" fill="#e4bc57"/></svg>
        +61 8 7142 5809
      </li>
      <li>
        <svg viewBox="0 0 12 12" aria-hidden="true"><circle cx="6" cy="6" r="6" fill="#1d1b1b"/><rect x="3" y="4" width="6" height="4.2" fill="#e4bc57"/><path d="M3 4l3 2.4L9 4" fill="none" stroke="#1d1b1b" stroke-width=".8"/></svg>
        belinda@theloombriefing.example
      </li>
      <li>
        <svg viewBox="0 0 12 12" aria-hidden="true"><circle cx="6" cy="6" r="6" fill="#1d1b1b"/><g fill="none" stroke="#e4bc57" stroke-width=".7"><circle cx="6" cy="6" r="3.4"/><ellipse cx="6" cy="6" rx="1.5" ry="3.4"/><path d="M2.6 6h6.8M3.1 4.4h5.8M3.1 7.6h5.8"/></g></svg>
        theloombriefing.example
      </li>
    </ul>
  </section>

</div>
</body>
</html>
```